KTWG application splash screen

We need a 1024x768 image for use as an application splash screen.
The image will be displayed full screen on an 10 inch industrial PC 1024x768 screen while our application is launching. The image should convey that the application is "Waiting for connection to Wi-Fi access point..." and include a graphic of the industrial PC connected to the access point via an Ethernet cable. A list of troubleshooting steps should be included at the bottom of the image. The troubleshooting steps should not be the main focus of the image and should be shown in a smaller font (but still readable at 1024x768 displayed on a 10 inch screen).
I will include a mock up of the general idea of what we are looking for as well as image files for the industrial PC, a screenshot of our application to show on the PC's screen and the AP.
For general look and feel and a sense of corporate branding please review our website https://marrowgatesoilworks.example/. The splash screen should reflect corporate branding.
Target Market(s)
Users of our application
Industry/Entity Type
Agriculture
Look and feel

```html
<!DOCTYPE html>
<html lang="en">
<head>
<meta charset="utf-8">
<title>KTWG – Waiting for Wi-Fi access point</title>
<link rel="stylesheet" href="https://fonts.googleapis.com/css2?family=Baloo+2:wght@700;800&family=Roboto:wght@400;500&display=swap">
<style>
  :root {
    --page: #ffffff;
    --screen-light: #f4f4f4;
    --screen-mid: #dcdcdc;
    --screen-dark: #b9b9b9;
    --brand-green: #5cb774;
    --ink: #111111;
    --text: #1c1c1c;
    --device-body: #2a2a2a;
    --device-screen: #dfe6e2;
    --ap-white: #f7f7f7;
    --figure-tone: #c9c9c9;
  }
  * { box-sizing: border-box; margin: 0; padding: 0; }
  html, body {
    width: 983px; height: 1200px; overflow: hidden;
    background: var(--page);
  }
  .splash {
    position: absolute; left: 0; top: 231px;
    width: 983px; height: 737px; overflow: hidden;
    background: radial-gradient(ellipse 70% 75% at 52% 32%, var(--screen-light) 0%, var(--screen-mid) 55%, var(--screen-dark) 100%);
    font-family: "Roboto", Arial, sans-serif;
    color: var(--text);
  }
  .headline {
    position: absolute; top: 146px;
    font-family: "Baloo 2", "Roboto", sans-serif;
    font-weight: 800; font-size: 31px; line-height: 36px;
  }
  .headline--lead { right: 527px; text-align: right; color: var(--brand-green); }
  .headline--target { left: 569px; color: var(--ink); }
  .wifi-icon { position: absolute; left: 411px; top: 37px; }
  .waiting-figure {
    position: absolute; left: 470px; top: 86px; width: 92px; height: 175px;
    border-radius: 40px 40px 12px 12px;
    background: linear-gradient(180deg, var(--figure-tone), #d8d8d8);
    opacity: .8;
  }
  .cab-computer {
    position: absolute; left: 61px; top: 271px; width: 221px; height: 177px;
    border-radius: 10px; background: var(--device-body);
    padding: 14px 20px 26px 20px;
  }
  .cab-computer__screen {
    width: 100%; height: 100%; border-radius: 2px;
    background: linear-gradient(180deg, #eef2f0, var(--device-screen));
  }
  .access-point {
    position: absolute; left: 842px; top: 203px; width: 26px; height: 216px;
    border-radius: 8px 8px 4px 4px;
    background: linear-gradient(90deg, #e6e6e6, var(--ap-white) 45%, #e2e2e2);
  }
  .cable { position: absolute; left: 0; top: 0; }
  .label {
    position: absolute; font-size: 17px; line-height: 21px; text-align: center;
    font-weight: 500; white-space: nowrap;
  }
  .label span { display: block; font-weight: 400; }
  .label--cable { left: 523px; top: 410px; transform: translateX(-50%); }
  .label--computer { left: 153px; top: 456px; transform: translateX(-50%); font-weight: 400; }
  .label--ap { left: 835px; top: 456px; transform: translateX(-50%); }
  .troubleshooting {
    position: absolute; left: 61px; top: 527px; width: 700px;
  }
  .troubleshooting__title { font-size: 17px; font-weight: 500; margin-bottom: 4px; }
  .steps { list-style: none; }
  .steps > li {
    position: relative; padding-left: 17px; font-size: 15.5px; line-height: 22px;
  }
  .steps > li::before {
    content: ""; position: absolute; left: 0; top: 6px;
    width: 11px; height: 11px; border-radius: 50%; background: var(--ink);
  }
  .substeps { list-style: none; margin-left: 10px; }
  .substeps li {
    position: relative; padding-left: 18px; font-size: 14.2px; line-height: 20.5px;
  }
  .substeps li::before {
    content: ""; position: absolute; left: 0; top: 5px;
    width: 10px; height: 10px; border-radius: 50%; background: var(--brand-green);
  }
  .brand {
    position: absolute; left: 813px; top: 636px;
    font-family: "Baloo 2", "Roboto", sans-serif; font-weight: 800;
    font-size: 42px; line-height: 48px; color: var(--brand-green);
    letter-spacing: 1px;
  }
</style>
</head>
<body>
<main class="splash">
  <svg class="wifi-icon" width="95" height="82" viewBox="0 0 95 82" aria-hidden="true">
    <g fill="none" stroke="var(--brand-green)" stroke-linecap="round">
      <path d="M6 74 A70 70 0 0 1 89 6" stroke-width="9"/>
      <path d="M30 74 A46 46 0 0 1 70 30" stroke-width="9"/>
      <path d="M52 72 A22 22 0 0 1 68 54" stroke-width="8"/>
    </g>
    <circle cx="71" cy="75" r="6" fill="var(--brand-green)"/>
  </svg>
  <div class="waiting-figure" role="img" aria-label="Illustration of a person sitting on a stool, waiting while looking at a phone"></div>

  <h1 class="headline headline--lead">Waiting for<br>connection to</h1>
  <p class="headline headline--target">Wi-Fi<br>access point...</p>

  <div class="cab-computer" role="img" aria-label="Tractor cab industrial computer showing the seeding application">
    <div class="cab-computer__screen"></div>
  </div>
  <div class="access-point" role="img" aria-label="Outdoor Wi-Fi access point with twin antennas"></div>

  <svg class="cable" width="983" height="737" aria-hidden="true">
    <polyline points="282,438 855,438 855,417" fill="none" stroke="var(--ink)" stroke-width="4"/>
  </svg>

  <p class="label label--cable" style="font-weight:400">Ethernet cable</p>
  <p class="label label--computer">Tractor<br>cab computer</p>
  <p class="label label--ap">Wi-Fi Access Point<span>Relaywave AX-200 Outdoor</span></p>

  <section class="troubleshooting">
    <h2 class="troubleshooting__title">TROUBLESHOOTING STEPS:</h2>
    <ul class="steps">
      <li>This screen should only be visible for a short time on boot.</li>
      <li>If this screen stays visible for more than a minute:
        <ul class="substeps">
          <li>Verify that the Wi-Fi Access Point (AP) powers up when this system does<br>(indicated by a green light on the side of the AP).</li>
          <li>Check the Ethernet cable between this system and the AP for damage, and replace it if necessary.</li>
          <li>Power-cycle this system and wait for it to reboot fully.</li>
          <li>If the issue persists, contact KTWG support for further assistance.</li>
        </ul>
      </li>
    </ul>
  </section>

  <p class="brand">KTWG</p>
</main>
</body>
</html>
```